LLC needs a business card design that emphasizes consulting and expert witness in upstream oil and g

I need a business card design for my company called Obena Consultative Service, LLC. My expertise is in oil and gas upstream operations management to optimize performance and also as an expert witness for law firms in oil and gas upstream operations litigation.
The final design should communicate knowledge and hands-on experience as well as trust. (Obena means rope or lasso. Perhaps "Obena" should be in the form of a rope.) I do not like the color green in any shade. My first preference would be some shade of blue.
Industry/Entity Type
Oil And Gas

```html
<!DOCTYPE html>
<html lang="en">
<head>
<meta charset="utf-8">
<title>Obena Consultative Service, LLC – Business Card</title>
<link href="https://fonts.googleapis.com/css2?family=Open+Sans:wght@400;600;700&display=swap" rel="stylesheet">
<style>
  :root {
    --backdrop: #2e2c2b;
    --card: #1c1d20;
    --card-back: #151618;
    --white: #ffffff;
    --text-soft: #e6e8ea;
    --blue: #3fa3e0;
    --divider: #3d6f8f;
    --mark-faint: #2a2c30;
  }
  * { margin: 0; padding: 0; box-sizing: border-box; }
  html, body {
    width: 1200px; height: 844px; overflow: hidden;
    background: var(--backdrop);
    font-family: "Open Sans", Arial, sans-serif;
  }
  .stage {
    position: relative; width: 1200px; height: 844px;
    display: flex; align-items: center; justify-content: center; gap: 60px;
  }
  .card {
    position: relative; width: 500px; height: 286px;
    box-shadow: 0 10px 30px rgba(0,0,0,.45);
  }
  .card-front { background: var(--card); }
  .card-back { background: var(--card-back); display: flex; align-items: center; justify-content: center; }

  .brand { position: absolute; left: 150px; top: 34px; color: var(--white); }
  .brand-name { font-size: 54px; font-weight: 600; line-height: 1; letter-spacing: 1px; }
  .brand-tagline { font-size: 16px; font-weight: 700; margin-top: 6px; }

  .person {
    position: absolute; right: 262px; top: 150px; text-align: right; color: var(--text-soft);
  }
  .person-name { font-size: 25px; font-weight: 600; color: var(--white); line-height: 1.15; }
  .person-title { font-size: 14px; color: var(--blue); margin-bottom: 10px; }
  .person-address { font-size: 14px; line-height: 1.35; }

  .divider {
    position: absolute; left: 252px; top: 150px; width: 1px; height: 108px; background: var(--divider);
  }

  .contacts { position: absolute; left: 266px; top: 148px; list-style: none; color: var(--text-soft); }
  .contacts li { display: flex; align-items: center; gap: 8px; font-size: 13px; line-height: 20px; }
  .contacts svg { width: 10px; height: 10px; fill: var(--blue); flex: none; }

  .back-name { font-size: 64px; font-weight: 600; color: var(--mark-faint); letter-spacing: 2px; }
</style>
</head>
<body>
<main class="stage">
  <section class="card card-front" aria-label="Card front">
    <div class="brand">
      <div class="brand-name">Obena</div>
      <div class="brand-tagline">Consultative Service, LLC</div>
    </div>

    <div class="person">
      <div class="person-name">Daniel Hart</div>
      <div class="person-title">Managing Director</div>
      <div class="person-address">12345, Address Goes Here<br>Country Name, 123456</div>
    </div>

    <div class="divider"></div>

    <ul class="contacts">
      <li><svg viewBox="0 0 10 10" aria-hidden="true"><path d="M1 3c0-1 1-2 4-2s4 1 4 2v1H7V3H3v1H1zM2 5h6l1 4H1z"/></svg>044-555 010 200</li>
      <li><svg viewBox="0 0 10 10" aria-hidden="true"><rect x="2" y="0.5" width="6" height="3"/><rect x="0.5" y="4" width="9" height="5" rx="1"/></svg>044-555 010 201</li>
      <li><svg viewBox="0 0 10 10" aria-hidden="true"><path d="M2.5 0h5v10h-5zM3.5 1v7h3V1z"/></svg>044-555 010 202</li>
      <li><svg viewBox="0 0 10 10" aria-hidden="true"><path d="M0 2h10v6H0zM1 3v.4l4 2.6 4-2.6V3L5 5.3z"/></svg>info@obenaconsult.com</li>
      <li><svg viewBox="0 0 10 10" aria-hidden="true"><path d="M6 1l3 3-2 2-1-1 1-1-1-1-3 3 1 1-1 1-1-1a1.4 1.4 0 010-2l2-2a1.4 1.4 0 012 0z"/></svg>www.obenaconsult.com</li>
    </ul>
  </section>

  <section class="card card-back" aria-label="Card back">
    <div class="back-name">Obena</div>
  </section>
</main>
</body>
</html>
```